Stationery Design Project

I need a design that is simple, clean and modern, in square style, bold font.
The majority of the design needs to be White and Black with a splash of Red colour.
I would like a design for business cards and letter heads with the following information.
Name, Title, Phone, Fax, Email, Website and company ABN number

Target Market(s)

25 to 65 years old real estate clients

Industry/Entity Type

Business

Requirements
Must have
• All designs must incorporate Company Logo, Name, Title, Phone, Fax, Email, Website and company ABN number

```html
<!DOCTYPE html>
<html lang="en">
<head>
<meta charset="utf-8">
<title>Harbour Crest Real Estate – Business Card</title>
<link href="https://fonts.googleapis.com/css2?family=Open+Sans:wght@400;600;700&display=swap" rel="stylesheet">
<style>
  :root {
    --brand-red: #d92a28;
    --ink: #1c1c1c;
    --muted-ink: #3a3a3a;
    --paper: #ffffff;
    --backdrop: #ecebe8;
    --rule: #555555;
  }
  * { box-sizing: border-box; margin: 0; padding: 0; }
  html, body {
    width: 1200px; height: 402px; overflow: hidden;
    background: var(--backdrop);
    font-family: "Open Sans", Arial, sans-serif;
  }
  .stage { position: relative; width: 1200px; height: 402px; }

  .card {
    position: absolute; top: 47px;
    height: 292px; border-radius: 22px; overflow: hidden;
  }

  /* Front */
  .card--front { left: 66px; width: 550px; background: var(--paper); }
  .front-swoosh { position: absolute; inset: 0; width: 100%; height: 100%; }
  .holder { position: absolute; right: 56px; top: 28px; text-align: right; color: var(--paper); }
  .holder__name { font-size: 20px; font-weight: 700; line-height: 1.1; }
  .holder__title { font-size: 15px; font-weight: 400; line-height: 1.3; }

  .wordmark { position: absolute; color: var(--ink); font-weight: 600; text-align: center; white-space: nowrap; }
  .wordmark__name { display: block; letter-spacing: 1px; }
  .wordmark__tag { display: block; letter-spacing: 7px; }
  .card--front .wordmark { left: 36px; top: 100px; width: 210px; }
  .card--front .wordmark__name { font-size: 23px; line-height: 1.1; }
  .card--front .wordmark__tag { font-size: 10px; margin-top: 8px; }

  .contacts { position: absolute; left: 34px; top: 210px; list-style: none; font-size: 13px; color: var(--muted-ink); }
  .contacts li { display: flex; align-items: center; gap: 5px; height: 17px; white-space: nowrap; }
  .contacts svg { width: 11px; height: 11px; fill: var(--brand-red); flex: none; }
  .divider { position: absolute; left: 189px; top: 238px; width: 1px; height: 42px; background: var(--rule); }
  .address { position: absolute; left: 211px; top: 242px; font-size: 13px; color: var(--muted-ink); line-height: 17px; }

  /* Back */
  .card--back { left: 633px; width: 512px; background: var(--brand-red); }
  .card--back .wordmark { color: var(--paper); left: 0; width: 100%; top: 98px; }
  .card--back .wordmark__name { font-size: 40px; line-height: 1.1; }
  .card--back .wordmark__tag { font-size: 14px; letter-spacing: 12px; margin-top: 10px; }
  .abn { position: absolute; left: 0; width: 100%; top: 236px; text-align: center; color: var(--paper); font-size: 16px; }
</style>
</head>
<body>
<main class="stage">
  <section class="card card--front">
    <svg class="front-swoosh" viewBox="0 0 550 292" preserveAspectRatio="none" aria-hidden="true">
      <path d="M0,0 H550 V145 C430,80 250,48 90,52 C50,53 20,56 0,60 Z" fill="var(--brand-red)"/>
      <path d="M0,62 C60,40 200,38 330,68 C250,50 120,48 0,70 Z" fill="#111"/>
    </svg>
    <div class="holder">
      <p class="holder__name">Your name</p>
      <p class="holder__title">Title</p>
    </div>
    <div class="wordmark">
      <span class="wordmark__name">HARBOUR CREST</span>
      <span class="wordmark__tag">REAL ESTATE</span>
    </div>
    <ul class="contacts">
      <li><svg viewBox="0 0 12 12"><path d="M3 1l2 2.5-1.2 1.2a7 7 0 0 0 3.5 3.5L8.5 7 11 9l-1.2 1.8C5.5 10.5 1.5 6.5 1.2 2.2Z"/></svg>123-456-7890</li>
      <li><svg viewBox="0 0 12 12"><path d="M3 1h6v3H3zM1 5h10v4H9v2H3V9H1zM4 8v2h4V8z"/></svg>123-456-7890</li>
      <li><svg viewBox="0 0 12 12"><path d="M1 3h10v6H1zM1.5 3.5 6 7l4.5-3.5"/></svg>info@hcmail.com</li>
      <li><svg viewBox="0 0 12 12"><circle cx="6" cy="6" r="5"/></svg>www.website.com</li>
    </ul>
    <span class="divider"></span>
    <p class="address">Street Name, City Name<br>State, City Zip Code</p>
  </section>

  <section class="card card--back">
    <div class="wordmark">
      <span class="wordmark__name">HARBOUR CREST</span>
      <span class="wordmark__tag">REAL ESTATE</span>
    </div>
    <p class="abn">ABN;123456789</p>
  </section>
</main>
</body>
</html>
```